Poloshirt Packaging

We need a very attractive packaging design for our poloshirts. We are wholesaler of the schoolwear market. See what we currently have. I dont want any specific sizing put on the packaging. One design for all poloshirts (2 sides).
our logo is attached aswell

Target Market(s)

Parents

Requirements
Must have
• Our logo
Should not have
• size or age

```html
<!DOCTYPE html>
<html lang="en">
<head>
<meta charset="utf-8">
<title>Brightwell Poloshirt Packaging</title>
<link rel="stylesheet" href="https://fonts.googleapis.com/css2?family=Poppins:wght@500;600&display=swap">
<style>
  :root {
    --navy: #163a63;
    --red: #e2232f;
    --wave-start: #e43a2a;
    --wave-mid: #ef7f1d;
    --wave-end: #f7c00f;
    --paper: #ffffff;
    --frame: #333333;
  }
  html, body {
    margin: 0;
    padding: 0;
    overflow: hidden;
    background: var(--paper);
  }
  .pack-face {
    position: relative;
    width: 849px;
    height: 1200px;
    box-sizing: border-box;
    border: 1px solid var(--frame);
    background: var(--paper);
    overflow: hidden;
    font-family: "Poppins", sans-serif;
  }
  .waves {
    position: absolute;
    inset: 0;
    width: 849px;
    height: 1200px;
  }
  .brand-name {
    position: absolute;
    left: 78px;
    top: 748px;
    margin: 0;
    font-size: 116px;
    font-weight: 600;
    line-height: 1;
    letter-spacing: -1px;
    color: var(--navy);
  }
  .product-type {
    position: absolute;
    left: 80px;
    top: 890px;
    margin: 0;
    font-size: 62px;
    font-weight: 600;
    line-height: 1;
    letter-spacing: 1px;
    color: var(--red);
  }
  .feature-bar {
    position: absolute;
    left: 81px;
    top: 979px;
    width: 529px;
    height: 26px;
    box-sizing: border-box;
    padding: 0 10px;
    background: var(--navy);
    color: var(--paper);
    font-size: 15px;
    font-weight: 500;
    line-height: 26px;
    white-space: nowrap;
    display: flex;
    justify-content: space-between;
  }
</style>
</head>
<body>
  <main class="pack-face">
    <svg class="waves" viewBox="0 0 849 1200" aria-hidden="true">
      <defs>
        <linearGradient id="sunset-wave" x1="0" y1="0" x2="1" y2="0">
          <stop offset="0" stop-color="var(--wave-start)"/>
          <stop offset="0.55" stop-color="var(--wave-mid)"/>
          <stop offset="1" stop-color="var(--wave-end)"/>
        </linearGradient>
      </defs>
      <path class="wave-upper" fill="url(#sunset-wave)"
        d="M0,587 C60,540 115,508 175,508 C330,508 450,470 620,285 C690,215 760,220 849,320 L849,376 C820,358 790,340 745,350 C680,365 620,430 564,504 C480,612 340,650 220,632 C140,620 70,668 0,726 Z"/>
      <path class="wave-lower" fill="var(--red)"
        d="M504,1200 C560,1190 610,1160 640,1110 C690,1040 760,1010 849,1008 L849,1080 C790,1088 750,1110 700,1165 L675,1200 Z"/>
    </svg>

    <h1 class="brand-name">Brightwell</h1>
    <p class="product-type">POLOSHIRT</p>
    <div class="feature-bar">
      <span>Superior weight fabric</span><span>|</span><span>Easy Care - Low iron</span><span>|</span><span>Reactive Dyes</span>
    </div>
  </main>
</body>
</html>
```